Ferncrest Roam Wording For Logo & Business card

I have the logo, I just need the "Ferncrest Roam" wording to go with it, and a business card design. The only thing on the business card is the website info. We provide nature connection experiences, and bolster these efforts through writing and host a platform for community around it.

I also have an idea of what it could look like (sketch), though I'm really not sure how it would come out. I am open to the best design and happy to consider original artwork. You can see what the site is about at FerncrestRoam.example.

Contact Information for Business Card

The only thing on the business card is the website info and the design. I will put other messaging on the back.

Website lettering (FerncrestRoam.example) in Montserrat

Logo Text

Ferncrest Roam (letters optional)

Font styles to use
Other font styles liked:
• montserrat

```html
<!DOCTYPE html>
<html lang="en">
<head>
<meta charset="utf-8">
<title>Ferncrest Roam — Business Card</title>
<link href="https://fonts.googleapis.com/css2?family=Montserrat:wght@500;600;700;800&display=swap" rel="stylesheet">
<style>
  :root {
    --bg: #3a3532;
    --purple: #3b1f5c;
    --purple-deep: #2f1850;
    --orange: #f07a1a;
    --orange-deep: #e2461b;
    --white: #ffffff;
    --text-light: #f3eef8;
  }
  * { box-sizing: border-box; margin: 0; padding: 0; }
  html, body { width: 1200px; height: 716px; overflow: hidden; }
  body {
    background: var(--bg);
    font-family: "Montserrat", sans-serif;
    display: flex;
    align-items: center;
    justify-content: center;
    gap: 40px;
  }
  .card {
    width: 540px;
    height: 309px;
    position: relative;
    overflow: hidden;
    box-shadow: 0 18px 40px rgba(0,0,0,.45);
  }
  /* Front */
  .card-front {
    background: var(--purple);
    border-bottom: 5px solid var(--orange);
    display: flex;
    align-items: center;
    justify-content: center;
    gap: 22px;
  }
  .brand-dot {
    width: 86px; height: 86px;
    border-radius: 50%;
    background: var(--purple-deep);
    border: 3px solid var(--orange);
    flex: none;
  }
  .brand-name {
    font-weight: 800;
    font-size: 38px;
    line-height: 1.05;
    letter-spacing: 1px;
    text-transform: uppercase;
    color: var(--white);
  }
  /* Back */
  .card-back { background: var(--white); }
  .back-wave { position: absolute; inset: 0; width: 100%; height: 100%; }
  .back-brand {
    position: absolute;
    left: 38px; top: 62px;
    width: 190px;
    display: flex;
    flex-direction: column;
    align-items: center;
    gap: 16px;
  }
  .back-brand .brand-dot { width: 70px; height: 70px; }
  .back-brand .brand-name {
    color: var(--purple);
    font-size: 27px;
    text-align: center;
  }
  .contact {
    position: absolute;
    left: 300px; right: 24px;
    top: 0; bottom: 0;
    display: flex;
    align-items: center;
    color: var(--text-light);
  }
  .contact-line {
    display: flex;
    align-items: center;
    gap: 8px;
    font-size: 13px;
    font-weight: 600;
    white-space: nowrap;
  }
  .contact-line svg { width: 13px; height: 13px; flex: none; fill: var(--orange); }
</style>
</head>
<body>
  <section class="card card-front" aria-label="Business card front">
    <span class="brand-dot"></span>
    <span class="brand-name">Ferncrest<br>Roam</span>
  </section>

  <section class="card card-back" aria-label="Business card back">
    <svg class="back-wave" viewBox="0 0 540 309" preserveAspectRatio="none" aria-hidden="true">
      <path d="M262 0 C222 60 240 130 210 200 C190 250 150 290 120 309 L540 309 L540 0 Z" fill="var(--orange-deep)"/>
      <path d="M278 0 C240 60 258 130 228 200 C208 250 168 290 140 309 L540 309 L540 0 Z" fill="var(--orange)"/>
      <path d="M292 0 C258 60 274 130 246 200 C226 250 188 290 162 309 L540 309 L540 0 Z" fill="var(--purple)"/>
    </svg>

    <div class="back-brand">
      <span class="brand-dot"></span>
      <span class="brand-name">Ferncrest<br>Roam</span>
    </div>

    <div class="contact">
      <p class="contact-line">
        <svg viewBox="0 0 24 24"><circle cx="12" cy="12" r="10"/></svg>
        www.ferncrestroam.example
      </p>
    </div>
  </section>
</body>
</html>
```